Clear Plastic Card Design

I am looking to have a business card designed from my logo icon. I am looking to match the style of a different business card I have attached in the files.
Looking for a card that is plastic, with layers of transparency in the shape of my logo icon (also attached in the files) - not a circle like the other card. The winning design will incorporate the red icon logo on the front and back and include the charity's name, "Light for the Weary Souls" in the same or similar font, as well as an email and phone number. For now, use the email: email@lightfortheweary-mail.org and the phone number 555-382-7194.
We like how the sample business card has transparency, partial and full opacity layers and a matching color scheme. Files will need to be in vector so that our business card printing company can work with it.
UPDATE:
We've some excellent designs in, thank you everyone! I got an early review from the owner, and he requested a minor redirect to find his perfect design. He wants the design to stand out by NOT being a rectangle. Try instead a circle, square, or best yet - something that falls in the outline of the logo icon, either fully or partially. Thank you, everyone!
Light for the Weary Souls text should be incorporated as well as a phone and email.

```html
<!DOCTYPE html>
<html lang="en">
<head>
<meta charset="utf-8">
<title>Light for the Weary Souls – Business Card</title>
<link href="https://fonts.googleapis.com/css2?family=Outfit:wght@400&family=Arimo:wght@400&display=swap" rel="stylesheet">
<style>
  :root {
    --backdrop: #606060;
    --card: #6f6f6f;
    --accent: #e0532a;
    --mark: #d2452a;
    --ink: #111111;
    --hands: #f4f4f4;
  }
  html, body {
    margin: 0;
    width: 1200px;
    height: 923px;
    overflow: hidden;
    background: var(--backdrop);
  }
  .card {
    position: absolute;
    left: 118px;
    top: 175px;
    width: 978px;
    height: 558px;
    border-radius: 51px;
    background: var(--card);
    overflow: hidden;
  }
  .edge-bar {
    position: absolute;
    top: 117px;
    width: 10px;
    height: 324px;
    background: var(--accent);
  }
  .edge-bar--left { left: 0; }
  .edge-bar--right { left: 968px; }
  .brand-mark {
    position: absolute;
    left: 718px;
    top: 86px;
    width: 160px;
    height: 160px;
    background: var(--mark);
  }
  .brand-name {
    position: absolute;
    right: 270px;
    top: 222px;
    margin: 0;
    font-family: "Outfit", sans-serif;
    font-weight: 400;
    font-size: 55px;
    line-height: 52px;
    color: var(--ink);
    text-align: left;
  }
  .hands-art {
    position: absolute;
    left: 779px;
    top: 306px;
    width: 178px;
    height: 252px;
    background: var(--hands);
  }
  .contact-icon {
    position: absolute;
    left: 49px;
    width: 40px;
    height: 40px;
  }
  .contact-icon--phone { top: 412px; }
  .contact-icon--email { top: 460px; }
  .contact-line {
    position: absolute;
    left: 106px;
    margin: 0;
    font-family: "Arimo", sans-serif;
    font-size: 33px;
    line-height: 33px;
    color: var(--ink);
    white-space: nowrap;
  }
  .contact-line--phone { top: 414px; }
  .contact-line--email { top: 461px; }
  .website {
    position: absolute;
    left: 243px;
    top: 505px;
    margin: 0;
    font-family: "Arimo", sans-serif;
    font-size: 33px;
    line-height: 33px;
    color: var(--accent);
    white-space: nowrap;
  }
</style>
</head>
<body>
  <div class="card">
    <span class="edge-bar edge-bar--left"></span>
    <span class="edge-bar edge-bar--right"></span>

    <div class="brand-mark"></div>
    <h1 class="brand-name">Light for the<br>Weary Souls</h1>

    <div class="hands-art" role="img" aria-label="Illustration of three raised hands"></div>

    <svg class="contact-icon contact-icon--phone" viewBox="0 0 40 40" aria-hidden="true">
      <circle cx="20" cy="20" r="18.5" fill="none" stroke="#111" stroke-width="2"/>
      <rect x="13.5" y="9" width="13" height="22" rx="2.5" fill="none" stroke="#111" stroke-width="2"/>
    </svg>
    <p class="contact-line contact-line--phone">555-382-7194</p>

    <svg class="contact-icon contact-icon--email" viewBox="0 0 40 40" aria-hidden="true">
      <circle cx="20" cy="20" r="18.5" fill="none" stroke="#111" stroke-width="2"/>
      <circle cx="20" cy="20" r="14" fill="#111"/>
      <rect x="11" y="14" width="18" height="12" rx="1.5" fill="#fff"/>
      <path d="M11.5 14.5 L20 21 L28.5 14.5" fill="none" stroke="#111" stroke-width="1.5"/>
    </svg>
    <p class="contact-line contact-line--email">email@lightfortheweary-mail.org</p>

    <p class="website">www.lightfortheweary.org</p>
  </div>
</body>
</html>
```